Barrister at Law needs Business Card Design

Need a business card design for Barrister at Law. Double sided. Simple Neil Thorsby and Barrister at Law on one side with contact details on the other side. I would like a professional design using Black or Platinum. Details on reverse side would include qualifications - Bcom-Llb and Acc Spec Commercial Litigation. I have attached the logo. Contact details would include address/ Po Box/ Phone/Fax/Mobile/email. I would like to use raised print or spot gloss.

```html
<!DOCTYPE html>
<html lang="en">
<head>
<meta charset="utf-8">
<title>Neil Thorsby — Barrister at Law</title>
<link href="https://fonts.googleapis.com/css2?family=Montserrat:wght@300;400;600;700;800&display=swap" rel="stylesheet">
<style>
  :root {
    --bg: #1c1c1e;
    --paper: #f1f1f1;
    --ink: #3a3a3c;
    --ink-soft: #8a8a8c;
    --band-1: #5b5b5d;
    --band-1-icon: #525254;
    --band-2: #6a6a6c;
    --band-2-icon: #606062;
    --band-3: #7a7a7c;
    --band-3-icon: #707072;
    --band-text: #f4f4f4;
    --accent: #b5d334;
    --back-top: #3a3a3d;
    --back-bottom: #1e1e20;
  }
  * { box-sizing: border-box; margin: 0; padding: 0; }
  html, body { width: 1200px; height: 900px; overflow: hidden; background: var(--bg); }
  body { font-family: "Montserrat", sans-serif; position: relative; }

  .card {
    position: absolute; top: 135px; width: 360px; height: 630px;
    overflow: hidden; box-shadow: 0 18px 40px rgba(0,0,0,.55);
  }
  .card--front { left: 180px; background: var(--paper); display: flex; flex-direction: column; }
  .card--back { left: 660px; background: linear-gradient(160deg, var(--back-top), var(--back-bottom)); }

  /* front */
  .identity { height: 300px; display: flex; flex-direction: column; justify-content: flex-end; padding: 0 34px 34px; }
  .identity__name { font-size: 34px; letter-spacing: 1px; color: var(--ink); line-height: 1; white-space: nowrap; }
  .identity__first { font-weight: 800; }
  .identity__last { font-weight: 300; color: var(--ink-soft); }
  .identity__role { margin-top: 9px; font-size: 11px; font-weight: 600; letter-spacing: 1.6px; color: var(--ink-soft); text-transform: uppercase; }
  .identity__quals { margin-top: 5px; font-size: 10px; font-weight: 400; letter-spacing: 1.2px; color: var(--ink-soft); text-transform: uppercase; }

  .contact-band { height: 96px; display: flex; color: var(--band-text); }
  .contact-band__icon { width: 78px; display: flex; align-items: center; justify-content: center; }
  .contact-band__text { flex: 1; display: flex; flex-direction: column; justify-content: center; padding-left: 16px; font-size: 12.5px; line-height: 1.45; font-weight: 400; white-space: nowrap; }
  .contact-band--address { background: var(--band-1); }
  .contact-band--address .contact-band__icon { background: var(--band-1-icon); }
  .contact-band--phone { background: var(--band-2); }
  .contact-band--phone .contact-band__icon { background: var(--band-2-icon); }
  .contact-band--web { background: var(--band-3); }
  .contact-band--web .contact-band__icon { background: var(--band-3-icon); }
  .contact-band__label { display: inline-block; width: 24px; font-weight: 600; }

  .edge-white { height: 12px; background: var(--paper); }
  .edge-accent { flex: 1; background: var(--accent); }

  /* back */
  .brand { position: absolute; top: 170px; left: 0; right: 0; display: flex; align-items: center; justify-content: center; gap: 14px; color: #fff; }
  .brand__mark { width: 40px; height: 40px; background: #fff; }
  .brand__name { font-size: 24px; font-weight: 700; letter-spacing: 1px; line-height: 1.05; text-transform: uppercase; }
  .back-strip { position: absolute; left: 0; right: 0; bottom: 0; height: 120px; background: var(--paper); border-top: 10px solid var(--accent); padding: 30px 30px 0; }
  .back-strip__name { font-size: 24px; font-weight: 800; color: var(--ink); text-transform: uppercase; letter-spacing: .5px; white-space: nowrap; }
  .back-strip__tagline { margin-top: 6px; font-size: 10.5px; font-weight: 400; letter-spacing: 1.6px; color: var(--ink-soft); text-transform: uppercase; }
</style>
</head>
<body>
  <section class="card card--front" aria-label="Card front">
    <div class="identity">
      <h1 class="identity__name"><span class="identity__first">NEIL</span> <span class="identity__last">THORSBY</span></h1>
      <p class="identity__role">Barrister at Law</p>
      <p class="identity__quals">BCom-LLB · Acc Spec Commercial Litigation</p>
    </div>

    <div class="contact-band contact-band--address">
      <div class="contact-band__icon">
        <svg width="22" height="30" viewBox="0 0 22 30" aria-hidden="true">
          <path d="M11 1a10 10 0 0 0-10 10c0 7 10 18 10 18s10-11 10-18A10 10 0 0 0 11 1z" fill="#e6e6e6"/>
          <circle cx="11" cy="11" r="4" fill="var(--band-1-icon)"/>
        </svg>
      </div>
      <div class="contact-band__text"><span>48 Kestrel Lane</span><span>Ashford 60712</span><span>PO Box 2219, Ashford 60713</span></div>
    </div>

    <div class="contact-band contact-band--phone">
      <div class="contact-band__icon">
        <svg width="34" height="28" viewBox="0 0 34 28" aria-hidden="true">
          <path d="M3 9c0-4 6-6 14-6s14 2 14 6v3h-7V9H10v3H3z" fill="#e6e6e6"/>
          <path d="M9 13h16l4 13H5z" fill="#e6e6e6"/>
          <circle cx="17" cy="19" r="3.5" fill="var(--band-2-icon)"/>
        </svg>
      </div>
      <div class="contact-band__text">
        <span><span class="contact-band__label">T</span>+000 - 4410 - 2836</span>
        <span><span class="contact-band__label">F</span>+000 - 4410 - 2837</span>
        <span><span class="contact-band__label">M</span>+000 - 7182 - 5390</span>
      </div>
    </div>

    <div class="contact-band contact-band--web">
      <div class="contact-band__icon">
        <svg width="32" height="32" viewBox="0 0 32 32" aria-hidden="true" fill="none" stroke="#e6e6e6" stroke-width="2">
          <circle cx="16" cy="16" r="14"/>
          <ellipse cx="16" cy="16" rx="6" ry="14"/>
          <line x1="2" y1="16" x2="30" y2="16"/>
          <line x1="16" y1="2" x2="16" y2="30"/>
          <path d="M5 9h22M5 23h22"/>
        </svg>
      </div>
      <div class="contact-band__text"><span>office@thorsbychambers.com</span><span>thorsbychambers.com</span></div>
    </div>

    <div class="edge-white"></div>
    <div class="edge-accent"></div>
  </section>

  <section class="card card--back" aria-label="Card back">
    <div class="brand">
      <span class="brand__mark"></span>
      <span class="brand__name">Thorsby<br>Chambers</span>
    </div>
    <div class="back-strip">
      <p class="back-strip__name">Thorsby Chambers</p>
      <p class="back-strip__tagline">Barrister at Law</p>
    </div>
  </section>
</body>
</html>
```